Business card update

Opening a subsidiary of my company in the USA and need to update my logo.
Updates

Reason: Give more time to a good design.

I made a mistake on my briefing. It's only the business card. Thanks for alerting me on the mistake.

All the best

Teodoro

Target Market(s)

We are an Executive Search company and our target audience are executives in large corporations.

Industry/Entity Type

Business

Requirements
Must have
• Keep the logo. In the US the company is called Delia Brunet Executive Search.

```html
<!DOCTYPE html>
<html lang="en">
<head>
<meta charset="utf-8">
<title>Delia Brunet Executive Search — Business Card</title>
<link href="https://fonts.googleapis.com/css2?family=Questrial&display=swap" rel="stylesheet">
<style>
  :root {
    --backdrop: #e6e9ea;
    --card-white: #ffffff;
    --mint: #48e4b1;
    --mint-deep: #2aa77f;
    --navy: #2b3a6e;
    --ink: #1e2a2a;
    --phone-red: #d8231f;
  }
  * { margin: 0; padding: 0; box-sizing: border-box; }
  html, body {
    width: 1200px; height: 741px; overflow: hidden;
    background: var(--backdrop);
    font-family: "Questrial", "Century Gothic", sans-serif;
  }
  .card {
    position: absolute; left: 100px; top: 80px;
    width: 1000px; height: 580px;
    background: var(--card-white);
    overflow: hidden;
  }
  .card__panel {
    position: absolute; left: 235px; top: 159px; right: 0; bottom: 0;
    background: var(--mint);
  }
  .brand {
    position: absolute; right: 24px; top: 70px;
    display: flex; align-items: center; gap: 16px;
  }
  .brand__dot { width: 22px; height: 22px; border-radius: 50%; background: var(--mint); }
  .brand__name {
    font-size: 40px; letter-spacing: 9px; color: var(--navy); line-height: 1;
  }
  .holder {
    position: absolute; top: 180px; font-size: 40px; line-height: 1;
  }
  .holder__first { right: 775px; color: var(--mint); }
  .holder__last { left: 242px; color: var(--card-white); }
  .phone {
    position: absolute; left: 53px; top: 248px;
    display: flex; align-items: center; gap: 12px;
    font-size: 31px; color: var(--ink);
  }
  .phone svg { width: 26px; height: 28px; }
  .company {
    position: absolute; right: 16px; top: 406px;
    font-size: 47px; color: var(--mint-deep); line-height: 1; white-space: nowrap;
  }
  .contact {
    position: absolute; left: 246px; right: 18px; top: 480px;
    display: flex; justify-content: space-between;
    font-size: 22px; line-height: 34px; color: var(--ink);
  }
  .contact__web { text-align: right; }
</style>
</head>
<body>
  <div class="card">
    <div class="card__panel"></div>

    <div class="brand">
      <span class="brand__dot"></span>
      <span class="brand__name">DELIA BRUNET</span>
    </div>

    <span class="holder holder__first">Teodoro</span>
    <span class="holder holder__last">S. Brunet</span>

    <div class="phone">
      <svg viewBox="0 0 24 26" aria-hidden="true">
        <path fill="var(--phone-red)" d="M6 1c1.5-.6 2.6.2 3.2 1.6l1.6 3.8c.5 1.2.1 2.2-1 2.9L8.5 10c.9 2.5 2.6 4.8 4.8 6.4l1.3-1.2c1-.9 2.1-1 3.1-.2l3.1 2.6c1.1.9 1.1 2.2.1 3.2l-1.6 1.7c-1.5 1.5-3.6 1.7-5.7.6C7.6 20 3.4 14 2.5 7.5 2.1 4.8 3.2 2.2 6 1z"/>
      </svg>
      <span>305 555-0148</span>
    </div>

    <div class="company">Delia Brunet Executive Search</div>

    <div class="contact">
      <div class="contact__address">4410 Harbor Blvd Suite 300<br>Bayview FL 33100</div>
      <div class="contact__web">www.dbexecutivesearch.com<br>tbrunet@dbexecutivesearch.com</div>
    </div>
  </div>
</body>
</html>
```